KRL Stationery Design Project

Dear Designers,
We need a new stationery design for company to match our new logo.
Designers should provide a design for the following:
1. Business Card: 3.5x2 Inches.
2. Letterhead: A4 size.
3. Envelops: 25x35.5 Cm.
You can keep the Arabic name at the bottom of the logo Or you can use the separate attached Arabic Name.
Please refer to the attached logo guide for design information.
Sample Business Card information:
Name: Tarek Sowan
Position: Operation Manager
Tel: +966 920007164 Ex. 500
Fax: +966 (3)8842617
Mob: +966 (5)00263817
email: tarek@krl-example.com.sa
URL: www.krl-example.com.sa
Address:
Nakheel Heights, Suite 718
Zayed bin Omar Str.
Khobar, 31847
Saudi Arabia
Updates
Dear All,
Please note, we had uploaded our logo along with Arabic writing in Adobe illustrator format (.ai).
Regards,
Karim
Dear All,
A sample data for the business card had been added as per your request.
Regards,
Karim

```html
<!DOCTYPE html>
<html lang="en">
<head>
<meta charset="utf-8">
<title>KRL Business Card</title>
<link rel="stylesheet" href="https://fonts.googleapis.com/css2?family=Source+Sans+3:wght@400;700&display=swap">
<style>
  :root {
    --navy: #0d2e52;
    --ink: #333333;
    --rule: #3a3a3a;
    --card: #ffffff;
    --backdrop: #2b2b2b;
    --sky-soft: #dfe6ee;
  }
  * { margin: 0; padding: 0; box-sizing: border-box; }
  html, body {
    width: 960px;
    height: 1200px;
    overflow: hidden;
    background: var(--backdrop);
    font-family: "Source Sans 3", sans-serif;
  }
  .canvas { position: relative; width: 960px; height: 1200px; }
  .card {
    position: absolute;
    left: 60px;
    width: 840px;
    height: 480px;
    background: var(--card);
    border-radius: 30px;
    overflow: hidden;
  }
  .card--front { top: 88px; }
  .card--back { top: 643px; }

  .brand-title {
    position: absolute;
    left: 60px;
    top: 40px;
    font-size: 64px;
    font-weight: 700;
    color: var(--navy);
    letter-spacing: 2px;
  }

  .contact-block {
    position: absolute;
    left: 63px;
    top: 180px;
    width: 300px;
    height: 270px;
    border-left: 1.5px solid var(--rule);
  }
  .contact-block .divider {
    position: absolute;
    left: -28px;
    top: 75px;
    width: 293px;
    border-top: 1.5px solid var(--rule);
  }
  .person { position: absolute; left: 9px; top: 8px; color: var(--ink); }
  .person-name { font-size: 25px; line-height: 30px; }
  .person-role { font-size: 19px; line-height: 26px; }

  .contact-list { position: absolute; left: 9px; top: 84px; list-style: none; }
  .contact-list li {
    position: relative;
    font-size: 19.5px;
    line-height: 28px;
    color: var(--ink);
  }
  .contact-list li.address { margin-top: 8px; line-height: 29px; }
  .contact-list .icon {
    position: absolute;
    left: -29px;
    top: 7px;
    width: 15px;
    height: 15px;
  }

  .art-satellite {
    position: absolute;
    left: 520px;
    top: 140px;
    width: 220px;
    height: 125px;
    background: linear-gradient(160deg, var(--sky-soft), #b8c6d6);
    border-radius: 6px;
  }
  .art-vehicle {
    position: absolute;
    left: 0;
    top: 0;
    width: 840px;
    height: 480px;
  }

  .back-mark {
    position: absolute;
    left: 0;
    right: 0;
    top: 175px;
    text-align: center;
    font-size: 96px;
    font-weight: 700;
    color: var(--navy);
    letter-spacing: 4px;
  }
</style>
</head>
<body>
<main class="canvas">

  <section class="card card--front">
    <h1 class="brand-title">KRL</h1>

    <div class="contact-block">
      <div class="divider"></div>
      <div class="person">
        <p class="person-name">Your Name</p>
        <p class="person-role">Designation</p>
      </div>
      <ul class="contact-list">
        <li>
          <svg class="icon" viewBox="0 0 16 16"><path fill="var(--ink)" d="M1 6c0-2 3-4 7-4s7 2 7 4v1h-4V5H5v2H1zM3 8h10l1 6H2z"/></svg>
          123-123-1234
        </li>
        <li>
          <svg class="icon" viewBox="0 0 16 16"><path fill="var(--ink)" d="M4 1h8v4H4zM1 6h14v6h-3v3H4v-3H1zM5 10v4h6v-4z"/></svg>
          123-123-1234
        </li>
        <li>
          <svg class="icon" viewBox="0 0 16 16"><text x="8" y="13" text-anchor="middle" font-size="14" font-weight="700" fill="var(--ink)" font-family="Source Sans 3, sans-serif">@</text></svg>
          info@krl-example.com.sa
        </li>
        <li>
          <svg class="icon" viewBox="0 0 16 16"><circle cx="8" cy="8" r="7" fill="var(--ink)"/><path d="M1 8h14M8 1v14M3 4h10M3 12h10" stroke="#fff" stroke-width="0.8" fill="none"/></svg>
          www.krl-example.com.sa
        </li>
        <li class="address">
          <svg class="icon" viewBox="0 0 16 16"><path fill="var(--ink)" d="M8 1l7 7h-2v7H10v-5H6v5H3V8H1z"/></svg>
          1234, Suite# 123, Street Name<br>tate Name, Country Code
        </li>
      </ul>
    </div>

    <div class="art-satellite" role="img" aria-label="Satellite illustration with signal waves"></div>
    <svg class="art-vehicle" viewBox="0 0 840 480" role="img" aria-label="Tracked truck with antenna on a rising slope">
      <polygon points="435,480 840,280 840,480" fill="var(--navy)"/>
    </svg>
  </section>

  <section class="card card--back">
    <p class="back-mark">KRL</p>
  </section>

</main>
</body>
</html>
```